Advertising company unique advertising platform

we need a logo design for a new company based in Australia Melbourne. We develop innovated advertising platform where consumer can use this platform to get regular discount, as business owner they can use this platform for free advertisement. Payment for this advertisement platform only payable every two weeks, when I generate revenue for their business

Industry/Entity Type

Advertising

Contact Information for Business Card

Dale Morven | Co-Founder |Managing Director
Suite 718 240 Wattlebrook Lane Melbourne Vic 3000

ABN 38 614 207 923
Tel: +61 0487 259 318 | Email: dale.morven@plivorantu.com

Font styles to use
Decorative
Script

Requirements
Must have
• Try few different design and some round corner business card
Should not have
• One round corner business card...try 4 different colour background not only black, make sure two side is designed. Be creative so imagine you are giving this to a client make sure has wow factor, if you can also try one design with engrave like all the logo, words look 3d feel
• The word Advertising Platform use attached file font

```html
<!DOCTYPE html>
<html lang="en">
<head>
<meta charset="utf-8">
<title>Tallora Hub — Business Card</title>
<link href="https://fonts.googleapis.com/css2?family=Marcellus&family=Montserrat:wght@400;500&display=swap" rel="stylesheet">
<style>
  :root {
    --page: #e9e6e1;
    --card-dark: #2a2a2b;
    --card-dark-edge: #1f1f20;
    --card-light: #ffffff;
    --accent-orange: #f07c22;
    --ink: #2b2b2b;
    --ink-soft: #4a4a4a;
    --wave-teal: #7fd9b4;
    --wave-blue: #6f9fe8;
  }
  * { margin: 0; padding: 0; box-sizing: border-box; }
  html, body { width: 1200px; height: 900px; overflow: hidden; }
  body {
    background: var(--page);
    position: relative;
    font-family: "Montserrat", Arial, sans-serif;
  }
  .card {
    position: absolute;
    width: 560px;
    height: 320px;
    border-radius: 18px;
    overflow: hidden;
    box-shadow: 0 14px 30px rgba(0,0,0,0.22);
  }
  .card--front {
    left: 80px; top: 90px;
    background: radial-gradient(ellipse at 50% 45%, #353536 0%, var(--card-dark) 55%, var(--card-dark-edge) 100%);
  }
  .card--back {
    left: 560px; top: 470px;
    background: var(--card-light);
  }
  .brand {
    position: absolute;
    display: flex;
    align-items: center;
    gap: 12px;
    font-family: "Marcellus", Georgia, serif;
    color: var(--accent-orange);
    white-space: nowrap;
  }
  .brand__dot {
    border-radius: 50%;
    background: var(--accent-orange);
    flex: none;
  }
  .card--front .brand {
    left: 50%; top: 50%;
    transform: translate(-50%, -50%);
    font-size: 44px;
  }
  .card--front .brand__dot { width: 38px; height: 38px; }
  .back__panel {
    position: absolute; inset: 0;
    width: 560px; height: 320px;
  }
  .card--back .brand {
    left: 370px; top: 58px;
    font-size: 28px;
  }
  .card--back .brand__dot { width: 24px; height: 24px; }
  .contact {
    position: absolute;
    left: 38px; top: 118px;
    color: var(--ink);
  }
  .contact__name {
    font-family: "Marcellus", Georgia, serif;
    font-size: 30px;
    color: var(--accent-orange);
    letter-spacing: 1px;
    text-transform: uppercase;
    line-height: 1;
  }
  .contact__role {
    font-family: "Marcellus", Georgia, serif;
    font-size: 11.5px;
    color: var(--ink-soft);
    text-transform: uppercase;
    margin-top: 6px;
    padding-bottom: 8px;
    border-bottom: 1.5px solid var(--accent-orange);
    width: 262px;
  }
  .contact__lines {
    margin-top: 12px;
    font-size: 13px;
    line-height: 1.5;
    font-weight: 500;
  }
  .contact__label { color: var(--accent-orange); }
  .contact__row { display: flex; align-items: center; gap: 8px; }
  .contact__icon { width: 12px; height: 12px; flex: none; }
</style>
</head>
<body>

  <section class="card card--front" aria-label="Card front">
    <div class="brand">
      <span class="brand__dot"></span>
      <span class="brand__name">Tallora Hub</span>
    </div>
  </section>

  <section class="card card--back" aria-label="Card back">
    <svg class="back__panel" viewBox="0 0 560 320" aria-hidden="true">
      <defs>
        <linearGradient id="wave-edge" x1="0" y1="0" x2="0" y2="1">
          <stop offset="0" stop-color="var(--wave-teal)"/>
          <stop offset="1" stop-color="var(--wave-blue)"/>
        </linearGradient>
        <radialGradient id="dark-fill" cx="0.6" cy="0.4" r="0.8">
          <stop offset="0" stop-color="#353536"/>
          <stop offset="1" stop-color="#232324"/>
        </radialGradient>
      </defs>
      <path d="M258 0 C 250 80, 330 110, 380 180 C 420 240, 425 290, 430 320 L 560 320 L 560 0 Z" fill="url(#dark-fill)"/>
      <path d="M258 0 C 250 80, 330 110, 380 180 C 420 240, 425 290, 430 320" fill="none" stroke="url(#wave-edge)" stroke-width="7"/>
    </svg>

    <div class="brand">
      <span class="brand__dot"></span>
      <span class="brand__name">Tallora Hub</span>
    </div>

    <div class="contact">
      <h1 class="contact__name">Dale Morven</h1>
      <p class="contact__role">Co-Founder | Managing Director</p>
      <div class="contact__lines">
        <p>Suite 718 240 Wattlebrook<br>Lane Melbourne Vic 3000</p>
        <p><span class="contact__label">ABN:</span> 38 614 207 923</p>
        <p class="contact__row">
          <svg class="contact__icon" viewBox="0 0 24 24" aria-hidden="true"><path d="M6.6 10.8a15.1 15.1 0 0 0 6.6 6.6l2.2-2.2a1 1 0 0 1 1-.25 11.4 11.4 0 0 0 3.6.57 1 1 0 0 1 1 1V20a1 1 0 0 1-1 1A17 17 0 0 1 3 4a1 1 0 0 1 1-1h3.5a1 1 0 0 1 1 1c0 1.25.2 2.45.57 3.57a1 1 0 0 1-.25 1z" fill="var(--accent-orange)"/></svg>
          +61 0487 259 318
        </p>
        <p class="contact__row">
          <svg class="contact__icon" viewBox="0 0 24 24" aria-hidden="true"><rect x="3" y="5" width="18" height="14" rx="2" fill="none" stroke="var(--accent-orange)" stroke-width="2.4"/><path d="M3.5 6l8.5 7 8.5-7" fill="none" stroke="var(--accent-orange)" stroke-width="2.4"/></svg>
          dale.morven@plivorantu.com
        </p>
      </div>
    </div>
  </section>

</body>
</html>
```